Computer consultant website

Plimvex Software is a newly started computer consulting company. It's a small one-man company that provides mostly Tablet applications but also websites in collaboration with designers. I'm running this company on the side of full time university studies.

I'm in need of a website which will function as:
Primarily - I'll direct potential clients to the page so they can read about the company, what i offer and past work.
Secondarily - Making my company visible through the web and maybe getting new clients.

The final design should look modern, clean and professional.

Pages that will be in the final website are (Note that it's not the exact titles as the page will not be in english):
* About
* Services (what Plimvex offers)
* Portfolio/work
* Short news (like ArtHivers "News and press")
* Contact.

Inspiration
http://www.arthiver.example/design/87836
http://www.brookwellstudio.example/
http://www.arthiver.example/design/845881
http://www.arthiver.example/design/1369424 - Lighter design, however a bit cluttered.

No programming code is needed delivered at all. Focus on designing rather then coding.

If you have any questions, do not hesitate to send me a message.

Target Market(s)

Non-technical entrepreneurs and small companies.

Industry/Entity Type

University

Requirements
Must have
• Must have my company logo (see attachment).

Must in any way use both colors from my logo.

A way to logically rearrange content to fit smaller screens. I will implement this design so that it can be pleasantly viewed on mobile devices. You don't necessarily need to provide exactly how the design would look on mobile devices.

I need the following types of page designs:
* Landing page
* Content page
* Portfolio/work (with accompanying inside/clicked) page

Landing/start page must in any way include at least the information:
* Shorter version of "About Plimvex"
* At least 1 most recent portfolio/work entry
* At least 1 most recent news entry
* Services that Plimvex offers.
Nice to have
• -
Should not have
• Testimonials or newsletter.

```html
<!DOCTYPE html>
<html lang="en">
<head>
<meta charset="utf-8">
<title>Plimvex Software</title>
<link rel="stylesheet" href="https://fonts.googleapis.com/css2?family=Ubuntu:wght@400;500;700&family=Questrial&display=swap">
<style>
:root{
  --blue:#1a73e0;
  --blue-dark:#0d4fb8;
  --hero-a:#2e6fd6;
  --hero-b:#1546a8;
  --ink:#3a3a3a;
  --muted:#555;
  --page:#f1f1f1;
  --card:#ffffff;
  --rule:#bdbdbd;
  --footer:#2b2b2b;
  --footer-text:#e0e0e0;
  --footer-muted:#9a9a9a;
}
*{box-sizing:border-box;margin:0;padding:0}
html,body{width:1133px;height:1200px;overflow:hidden}
body{position:relative;background:var(--page);font-family:"Ubuntu",sans-serif;color:var(--ink)}
.abs{position:absolute}
.topbar{left:0;top:0;width:1133px;height:19px;background:linear-gradient(90deg,#0b2236,#1b5d8a 50%,#0b2236)}
.brand{left:120px;top:55px;display:flex;align-items:center;gap:18px}
.brand-mark{width:86px;height:86px;border-radius:50%;background:var(--blue)}
.brand-name{font-size:58px;font-weight:500;color:#3b3b3b;letter-spacing:-1px}
.phone{left:571px;top:37px;display:flex;align-items:center;gap:12px;color:var(--blue-dark);font-size:21px}
.quote-call{left:580px;top:66px;font-size:19px;color:#333}
.search{left:777px;top:45px;width:257px;height:22px;display:flex;box-shadow:0 4px 6px rgba(0,0,0,.12)}
.search-input{flex:1;border:1px solid #cfcfcf;background:#fff;font-size:11px;color:#999;padding:3px 18px}
.search-btn{width:60px;background:var(--blue);color:#fff;font-size:11px;text-align:center;line-height:22px}
.nav{left:585px;top:103px;display:flex;align-items:center;font-size:13px;color:#333}
.nav-home{position:relative;width:74px;height:39px;background:var(--blue);color:#fff;border-radius:4px 4px 0 0;text-align:center;line-height:39px}
.nav-home::after{content:"";position:absolute;left:30px;bottom:-8px;border:8px solid transparent;border-bottom:0;border-top-color:var(--blue)}
.hero{left:84px;top:150px;width:956px;height:340px;background:radial-gradient(ellipse at 65% 45%,var(--hero-a),var(--hero-b) 80%);box-shadow:0 10px 12px -8px rgba(0,0,0,.45)}
.hero-title{left:165px;top:235px;font-size:25px;color:#fff;font-weight:400}
.hero-text{left:119px;top:277px;width:345px;font-size:13px;line-height:22.6px;color:#e8efff}
.hero-btn{left:245px;top:371px;width:164px;height:44px;border-radius:6px;background:linear-gradient(#2f8cf5,#1566d8);color:#fff;font-size:19px;text-align:center;line-height:44px;box-shadow:2px 4px 6px rgba(0,0,0,.35)}
.hero-visual{left:517px;top:189px;width:512px;height:264px;border-radius:22px;background:linear-gradient(135deg,#1c1c1c,#173a8a 45%,#2a5ad0 70%,#1b1b1b)}
.hero-stand{left:458px;top:456px;width:174px;height:34px;background:linear-gradient(#3a3a3a,#111);border-radius:18px 18px 0 0}
.dot{top:466px;width:13px;height:13px;border-radius:50%;background:#111;border:1px solid #555}
.dot.on{background:var(--blue)}
.card{top:514px;width:298px;height:150px;background:var(--card);border-radius:4px;box-shadow:0 1px 3px rgba(0,0,0,.08);overflow:hidden}
.card-title{position:absolute;left:11px;top:8px;font-size:17px;color:var(--blue);font-weight:400}
.card-rule{position:absolute;left:11px;top:36px;width:257px;height:1px;background:var(--rule)}
.card-icon{position:absolute;left:16px;top:56px;width:55px;height:55px;border-radius:50%;background:var(--blue);display:flex;align-items:center;justify-content:center}
.card-text{position:absolute;left:85px;top:54px;width:190px;font-size:11px;line-height:17px;color:var(--muted)}
.card-more{position:absolute;right:0;bottom:0;width:102px;height:27px;background:linear-gradient(#1f7ae8,#0e55c8);color:#fff;font-size:12px;text-align:center;line-height:27px;border-radius:4px 0 0 0}
.services{left:82px;top:687px;width:959px;height:345px;background:var(--card)}
.services-title{left:114px;top:719px;font-size:17px;color:var(--blue);font-weight:400}
.service{top:769px;width:200px}
.service-img{width:198px;height:113px;border:1px solid #d4d4d4;border-radius:8px}
.service-name{margin-top:8px;font-size:13px;color:#333;padding-left:7px;font-weight:400}
.service-text{margin-top:2px;font-size:11px;line-height:17px;color:var(--muted);padding-left:7px}
.service-more{margin:9px 0 0 9px;width:124px;height:30px;border:1px solid #e0e0e0;border-radius:3px;background:linear-gradient(#fff,#ededed);font-family:"Questrial",sans-serif;font-size:12px;color:#777;display:flex;align-items:center;justify-content:center;gap:8px;letter-spacing:.5px}
.service-more i{width:12px;height:12px;border-radius:50%;background:#bbb;display:inline-block}
.footer{left:0;top:1032px;width:1133px;height:168px;background:linear-gradient(#353535,var(--footer))}
.f-head{top:1061px;font-size:13px;color:var(--footer-text);font-weight:400}
.f-lines{font-size:12px;line-height:17px;color:var(--footer-text)}
.sitemap{left:349px;top:1084px;font-size:13px;line-height:22.7px;color:var(--footer-text);list-style:none}
.news{left:525px;top:1087px;width:205px;font-size:11px;line-height:17px;color:var(--footer-muted)}
.news-more{left:685px;top:1171px;font-size:11px;color:#5b9ef0}
.social{top:1060px;width:38px;height:38px;border-radius:50%;background:#3d3d3d;border:2px solid #6a6a6a}
.copyright{right:97px;top:1118px;font-size:11px;color:var(--footer-text)}
.scale{right:104px;top:1141px;font-size:11px;color:var(--footer-text)}
</style>
</head>
<body>
<div class="abs topbar"></div>

<header>
  <div class="abs brand"><span class="brand-mark"></span><span class="brand-name">Plimvex</span></div>
  <div class="abs phone">
    <svg width="26" height="22" viewBox="0 0 26 22"><path d="M4 2c2-1 4 0 5 2l1 3c0 1-1 2-2 3 1 3 4 6 7 7 1-1 2-2 3-2l3 1c2 1 3 3 2 5-1 2-3 2-5 1C10 19 5 13 3 7 2 5 2 3 4 2z" fill="#555"/></svg>
    <span>03 5550 1842</span>
  </div>
  <div class="abs quote-call">Free Quotes Call</div>
  <div class="abs search"><span class="search-input">type your word here</span><span class="search-btn">SEARCH</span></div>
  <nav class="abs nav">
    <span class="nav-home">Home</span>
    <span style="margin-left:16px">About</span>
    <span style="margin-left:39px">Services</span>
    <span style="margin-left:38px">Portfolio</span>
    <span style="margin-left:30px">News</span>
    <span style="margin-left:36px">Contact</span>
  </nav>
</header>

<section>
  <div class="abs hero"></div>
  <h1 class="abs hero-title">Tablet Apps</h1>
  <p class="abs hero-text">Nunc varius facilisis eros. Sed erat. In quis arcu ornare laoreet. luctus massa.Nunc varius facilisis eros. Sed erat. In quis arcu ornare laoreet. luctus massa.</p>
  <div class="abs hero-btn">Get it Now</div>
  <div class="abs hero-visual" role="img" aria-label="Photo of a tablet showing its home screen with apps, beside a green robot figure"></div>
  <div class="abs hero-stand"></div>
  <span class="abs dot on" style="left:509px"></span>
  <span class="abs dot" style="left:535px"></span>
  <span class="abs dot" style="left:561px"></span>
  <span class="abs dot" style="left:586px"></span>
</section>

<section>
  <article class="abs card" style="left:84px">
    <h2 class="card-title">ABOUT PLIMVEX</h2><div class="card-rule"></div>
    <div class="card-icon"><svg width="22" height="30" viewBox="0 0 22 30"><rect x="2" y="1" width="18" height="28" rx="3" fill="#111"/><rect x="5" y="5" width="12" height="7" fill="#1a73e0"/><g fill="#1a73e0"><rect x="5" y="15" width="3" height="3"/><rect x="10" y="15" width="3" height="3"/><rect x="15" y="15" width="2" height="3"/><rect x="5" y="20" width="3" height="3"/><rect x="10" y="20" width="3" height="3"/><rect x="15" y="20" width="2" height="3"/></g></svg></div>
    <p class="card-text">Lorem Ipsum has been the industry's standard dummy text ever since the when an unknown took a galley of type .</p>
    <span class="card-more">View More &gt;&gt;</span>
  </article>
  <article class="abs card" style="left:412px">
    <h2 class="card-title">MOST RECENT JOB</h2><div class="card-rule"></div>
    <div class="card-icon"><svg width="30" height="26" viewBox="0 0 30 26"><circle cx="15" cy="8" r="7" fill="#111"/><path d="M2 26c0-8 6-11 13-11s13 3 13 11z" fill="#111"/></svg></div>
    <p class="card-text">Lorem Ipsum has been the industry's standard dummy text ever since the when an unknown took a galley of type .</p>
    <span class="card-more">View More &gt;&gt;</span>
  </article>
  <article class="abs card" style="left:743px">
    <h2 class="card-title">MOST RECENT NEWS</h2><div class="card-rule"></div>
    <div class="card-icon"><svg width="26" height="28" viewBox="0 0 26 28"><rect x="7" y="1" width="17" height="22" fill="#333"/><path d="M2 7h15v20H2z" fill="#111"/></svg></div>
    <p class="card-text" style="top:44px">Lorem Ipsum has been the industry's standard dummy text ever since the when an unknown took a galley of type .</p>
    <span class="card-more">View More &gt;&gt;</span>
  </article>
</section>

<section>
  <div class="abs services"></div>
  <h2 class="abs services-title">SERVICES THAT PLIMVEX OFFERS</h2>
  <div class="abs service" style="left:109px">
    <div class="service-img" role="img" aria-label="Phone and tablet showing apps" style="background:linear-gradient(135deg,#3a4a6a,#8fa6c8 60%,#e8eef5)"></div>
    <h3 class="service-name">TABLET APPS</h3>
    <p class="service-text">Lorem Ipsum has been the industry's standard dummy text ever since the when an unknown took a galley of</p>
    <div class="service-more"><i></i>VIEW MORE</div>
  </div>
  <div class="abs service" style="left:340px">
    <div class="service-img" role="img" aria-label="Smartphone surrounded by app icons" style="background:linear-gradient(135deg,#f4f4f4,#6cc4f0 50%,#f4f4f4)"></div>
    <h3 class="service-name">MOBILE APPS</h3>
    <p class="service-text">Lorem Ipsum has been the industry's standard dummy text ever since the when an unknown took a galley of</p>
    <div class="service-more"><i></i>VIEW MORE</div>
  </div>
  <div class="abs service" style="left:582px">
    <div class="service-img" role="img" aria-label="Envelope with a green robot figure" style="background:linear-gradient(90deg,#f7f7f7,#e6e6e6 45%,#a4c93b 70%,#f7f7f7)"></div>
    <h3 class="service-name">EMAIL</h3>
    <p class="service-text">Lorem Ipsum has been the industry's standard dummy text ever since the when an unknown took a galley of</p>
    <div class="service-more"><i></i>VIEW MORE</div>
  </div>
  <div class="abs service" style="left:819px">
    <div class="service-img" role="img" aria-label="Hand drawing colourful artwork on a screen" style="background:linear-gradient(135deg,#f5f5f5,#7ab8e0 35%,#d8cfc4 65%,#f5f5f5)"></div>
    <h3 class="service-name">WEB DESIGN</h3>
    <p class="service-text">Lorem Ipsum has been the industry's standard dummy text ever since the when an unknown took a galley of</p>
    <div class="service-more"><i></i>VIEW MORE</div>
  </div>
</section>

<footer>
  <div class="abs footer"></div>
  <h4 class="abs f-head" style="left:113px">CONTACT US</h4>
  <p class="abs f-lines" style="left:116px;top:1090px">Loreum Ipsum Dollar<br>Sit amet</p>
  <p class="abs f-lines" style="left:116px;top:1138px">Phone : 03 5550 1842<br>Email : info@plimvex.example</p>
  <h4 class="abs f-head" style="left:349px">SITEMAP</h4>
  <ul class="abs sitemap"><li>Home</li><li>About</li><li>Services</li><li>Portfolio</li><li>News</li></ul>
  <h4 class="abs f-head" style="left:520px">LATEST NEWS</h4>
  <p class="abs news">Feb 28, 2013<br>Lorem Ipsum has been the industry's standard dummy text ever since the when an unknown took a galley of type .</p>
  <span class="abs news-more">MORE &gt;&gt;</span>
  <span class="abs social" style="left:817px"></span>
  <span class="abs social" style="left:863px"></span>
  <span class="abs social" style="left:908px"></span>
  <span class="abs social" style="left:955px"></span>
  <span class="abs social" style="left:1001px"></span>
  <p class="abs copyright">Copyright © 2013 Plimvex. All rights reserved.</p>
  <p class="abs scale">x2</p>
</footer>
</body>
</html>
```